Financial Advisor Resource Firm needs business card design

Need business card design for company in Omaha NE called Meridale Circle. We provide resources to financial advisors....workshop programs, retirement analysis, and insurance planning. I would like to see designs that use grays, greens, black, and white colors. The final design should communicate 'collaboration' and be simple yet attractive to financial planning clients. I will attached our logo and another picture of a puzzle piece coming together. I would like the incorporate the puzzle picture somehow, maybe on the back somehow, with color or just the gray scale....OR, the picture be the front of the card with 'Meridale' definition on it (see upload) and then company logo, employee name, title, address on the back (see ppt uploaded). The following disclosure needs to be included somewhere- Advisory services offered through Stonebrook Assets, LLC.
Updates

I uploaded a svg and ai file of the logo

Target Market(s)

Financial planning clients and financial advisors....so pretty diverse age range of about 40-70.

Industry/Entity Type

Financial Planning

Contact Information for Business Card

Tobias L. Fenwright, MBA
Founder/President
5287 E. Larkin Road
Suite 230
Omaha, NE 68190
Phone- (402) 555-0147
Cell- (402) 555-0183
Fax- (402) 555-0129
email- tobias@meridaleplan.example
web address- www.meridaleplan.example

Colors
1b1b1b
474747
d3d3d3
ffffff
9bcb3c
abd036

Requirements
Must have
• Must include logo provided, must be 2 sided, and must have disclosure...all of these items listed in project description

```html
<!DOCTYPE html>
<html lang="en">
<head>
<meta charset="utf-8">
<title>Meridale Circle – Business Card</title>
<link href="https://fonts.googleapis.com/css2?family=Montserrat:wght@400;500&display=swap" rel="stylesheet">
<style>
  :root{
    --canvas:#f3f3f3;
    --ink:#1b1b1b;
    --ink-soft:#474747;
    --paper:#f7f7f7;
    --green:#8dc63f;
    --green-bright:#9bcb3c;
    --white:#ffffff;
    --muted:#8a8a8a;
    --photo-light:#d3d3d3;
    --photo-mid:#9a9a9a;
    --photo-dark:#474747;
  }
  *{margin:0;padding:0;box-sizing:border-box}
  html,body{width:1200px;height:900px;overflow:hidden;background:var(--canvas)}
  body{position:relative;font-family:"Montserrat",Arial,sans-serif}
  .card{
    position:absolute;top:124px;width:372px;height:652px;overflow:hidden;
    box-shadow:0 4px 18px rgba(0,0,0,.28);
  }
  .card--front{left:186px;background:var(--ink)}
  .card--back{left:642px;background:var(--paper)}
  .card__art{position:absolute;left:0;top:0;width:372px;height:652px}
  .wordmark{
    position:absolute;left:0;width:100%;text-align:center;
    font-weight:400;text-transform:uppercase;white-space:nowrap;color:var(--white);
  }
  .card--front .wordmark{top:446px;font-size:27px;letter-spacing:2px;line-height:34px}
  .card--back .wordmark{top:131px;font-size:17px;letter-spacing:2px}
  .tagline{
    position:absolute;top:523px;left:0;width:100%;text-align:center;
    color:var(--white);font-size:16px;line-height:20px;
  }
  .tagline em{font-style:normal;color:var(--green)}
  .disclosure{
    position:absolute;left:0;top:624px;width:100%;text-align:center;
    color:var(--muted);font-size:8.5px;letter-spacing:.3px;
  }
  .contact{position:absolute;left:0;width:100%;text-align:center;color:#333}
  .contact__name{top:312px;font-size:22px;color:var(--green)}
  .contact__name small{font-size:16px;color:var(--ink-soft)}
  .contact__title{top:339px;font-size:15px;color:var(--ink-soft)}
  .contact__icons{top:375px;display:flex;justify-content:center;gap:8px}
  .contact__icons svg{width:18px;height:18px;fill:var(--green)}
  .contact__lines{top:409px;font-size:16px;line-height:25.3px}
  .contact__lines .accent{color:var(--green)}
  .address-band{
    position:absolute;left:0;top:574px;width:372px;height:78px;background:var(--green);
    color:var(--white);text-align:center;font-size:15.5px;line-height:21px;padding-top:15px;
  }
  .address-band__pin{
    position:absolute;left:156px;top:-26px;width:60px;height:60px;border-radius:50%;
    background:var(--green);display:flex;justify-content:center;padding-top:8px;
  }
  .address-band__pin svg{width:14px;height:19px;fill:var(--white)}
  .address-band__text{position:relative}
</style>
</head>
<body>

<section class="card card--front">
  <svg class="card__art" viewBox="0 0 372 652">
    <defs>
      <linearGradient id="frontPhoto" x1="0" y1="0" x2="1" y2="1">
        <stop offset="0" stop-color="var(--photo-mid)"/>
        <stop offset=".35" stop-color="var(--photo-light)"/>
        <stop offset=".7" stop-color="var(--photo-mid)"/>
        <stop offset="1" stop-color="var(--photo-dark)"/>
      </linearGradient>
    </defs>
    <path role="img" aria-label="Grayscale photo of hands joining puzzle pieces together" fill="url(#frontPhoto)"
      d="M0,0H372V264H340C326,264 322,276 318,292C302,332 252,360 186,360C120,360 70,332 54,292C50,276 46,264 32,264H0Z"/>
    <path fill="none" stroke="var(--green)" stroke-width="3.5"
      d="M30,262H36C48,262 50,276 54,292C70,332 120,360 186,360C252,360 302,332 318,292C322,276 324,262 336,262H342"/>
  </svg>
  <div class="wordmark">Meridale Circle</div>
  <p class="tagline">To come <em>TOGETHER</em> and <em>UNITE</em><br>in common interest<br>and <em>FOCUS</em></p>
  <p class="disclosure">Advisory services offered through Stonebrook Assets, LLC</p>
</section>

<section class="card card--back">
  <svg class="card__art" viewBox="0 0 372 652">
    <defs>
      <linearGradient id="backPhoto" x1="0" y1="0" x2="1" y2="1">
        <stop offset="0" stop-color="var(--photo-mid)"/>
        <stop offset=".4" stop-color="var(--photo-light)"/>
        <stop offset="1" stop-color="var(--photo-dark)"/>
      </linearGradient>
    </defs>
    <path role="img" aria-label="Grayscale photo of hands joining puzzle pieces together" fill="url(#backPhoto)"
      d="M0,0H372V190H336C320,190 318,202 314,216C296,258 246,286 186,286C126,286 76,258 58,216C54,202 52,190 36,190H0Z"/>
    <path fill="none" stroke="var(--green)" stroke-width="3.5"
      d="M26,189H34C48,189 52,202 56,216C74,258 126,287 186,287C246,287 298,258 316,216C320,202 324,189 338,189H346"/>
    <circle cx="186" cy="141" r="122" fill="var(--green-bright)" fill-opacity=".82"/>
  </svg>
  <div class="wordmark">Meridale Circle</div>

  <div class="contact contact__name">Tobias L. Fenwright<small>, MBA</small></div>
  <div class="contact contact__title">Founder | President</div>
  <div class="contact contact__icons">
    <svg viewBox="0 0 24 24" aria-label="Phone"><path d="M6.6 10.8a15 15 0 0 0 6.6 6.6l2.2-2.2a1 1 0 0 1 1-.25 11.4 11.4 0 0 0 3.6.57 1 1 0 0 1 1 1V20a1 1 0 0 1-1 1A17 17 0 0 1 3 4a1 1 0 0 1 1-1h3.5a1 1 0 0 1 1 1c0 1.25.2 2.45.57 3.57a1 1 0 0 1-.25 1Z"/></svg>
    <svg viewBox="0 0 24 24" aria-label="Mobile"><path d="M7 1h10a2 2 0 0 1 2 2v18a2 2 0 0 1-2 2H7a2 2 0 0 1-2-2V3a2 2 0 0 1 2-2Zm0 3v14h10V4Zm5 15.5a1 1 0 1 0 0 2 1 1 0 0 0 0-2Z"/></svg>
    <svg viewBox="0 0 24 24" aria-label="Fax"><path d="M3 6h4v16H3Zm6-4h9l3 3v17H9Zm2 6v3h8V8Zm0 6v2h2v-2Zm3 0v2h2v-2Zm3 0v2h2v-2Zm-6 3v2h2v-2Zm3 0v2h2v-2Zm3 0v2h2v-2Z"/></svg>
    <svg viewBox="0 0 24 24" aria-label="Email"><path d="M2 5h20v2l-10 6L2 7Zm0 4.3 10 6 10-6V19H2Z"/></svg>
    <svg viewBox="0 0 24 24" aria-label="Website"><path d="M12 2a10 10 0 1 0 0 20 10 10 0 0 0 0-20Zm-1 17.9A8 8 0 0 1 4.2 10L9 14.8v1a2 2 0 0 0 2 2Zm6.9-2.5A2 2 0 0 0 16 16h-1v-3a1 1 0 0 0-1-1H8v-2h2a1 1 0 0 0 1-1V7h2a2 2 0 0 0 2-2v-.4a8 8 0 0 1 2.9 12.8Z"/></svg>
  </div>
  <div class="contact contact__lines">
    (402) 555 - 0147<br>
    (402) 555 - 0183<br>
    (402) 555 - 0129<br>
    tobias@meridaleplan.example<br>
    www.<span class="accent">meridaleplan</span>.example
  </div>

  <div class="address-band">
    <div class="address-band__pin">
      <svg viewBox="0 0 14 19" aria-label="Location"><path d="M7 0a7 7 0 0 0-7 7c0 5 7 12 7 12s7-7 7-12a7 7 0 0 0-7-7Zm0 9.8A2.8 2.8 0 1 1 7 4.2a2.8 2.8 0 0 1 0 5.6Z"/></svg>
    </div>
    <div class="address-band__text">5287 E. Larkin Road<br>Suite 230, Omaha, NE 68190</div>
  </div>
</section>

</body>
</html>
```